TORV.
TORVALE ENTERTAINMENT & MEDIA
TORV. -
Creative Brief
Use specific fonts
any thing which suits with the LOGO provided
Professional
VIKRAM TULSE
MR.
D-47, WEST ENCLAVE-II , GURGAON 122001,HARYANA, INDIA
vikram@torv.co.in
www.torv.co.in
LOG IN THE CENTRE

```html
<!DOCTYPE html>
<html lang="en">
<head>
<meta charset="utf-8">
<title>TORV. Business Cards</title>
<link href="https://fonts.googleapis.com/css2?family=Arimo:wght@400;700&display=swap" rel="stylesheet">
<style>
  :root {
    --backdrop: #e4e1dc;
    --card: #ffffff;
    --band-dark: #16527e;
    --band-mid: #2b8bbf;
    --band-light: #5fb3d9;
    --brand: #1d5f93;
    --brand-deep: #173d63;
    --ink: #3d4650;
    --muted: #6c747c;
    --rule: #c9cdd1;
    --icon: #2a7db4;
  }
  * { margin: 0; padding: 0; box-sizing: border-box; }
  html, body { width: 1200px; height: 852px; overflow: hidden; }
  body {
    background: var(--backdrop);
    font-family: "Arimo", Arial, sans-serif;
    color: var(--ink);
    position: relative;
  }
  .card {
    position: absolute;
    width: 600px;
    height: 343px;
    background: var(--card);
    border-radius: 18px;
    overflow: hidden;
    box-shadow: 0 6px 18px rgba(0,0,0,0.18);
  }
  .card--vertical { left: 90px; top: 70px; }
  .card--horizontal { left: 510px; top: 440px; }
  .card__band {
    position: absolute;
    left: 0; top: 0; bottom: 0;
    width: 26px;
    background: linear-gradient(90deg, var(--band-dark), var(--band-mid) 60%, var(--band-light));
  }
  .card__divider {
    position: absolute;
    width: 1px;
    background: var(--rule);
  }
  .brand-mark {
    position: absolute;
    display: flex;
    align-items: center;
    color: var(--brand);
    font-weight: 700;
    letter-spacing: 1px;
  }
  .brand-mark__square {
    background: var(--brand-deep);
    flex: none;
  }
  .card--vertical .brand-mark {
    left: 80px; top: 100px; width: 200px;
    flex-direction: column;
    font-size: 56px;
    gap: 14px;
  }
  .card--vertical .brand-mark__square { width: 52px; height: 52px; }
  .card--vertical .card__divider { left: 300px; top: 40px; height: 270px; }
  .details {
    position: absolute;
  }
  .card--vertical .details { left: 322px; top: 36px; }
  .details__name {
    color: var(--brand);
    font-weight: 700;
    font-size: 19px;
    letter-spacing: 0.3px;
    margin-bottom: 26px;
  }
  .details__address {
    font-size: 14px;
    line-height: 1.45;
    color: var(--muted);
    margin-bottom: 22px;
  }
  .contacts { list-style: none; }
  .contacts li {
    display: flex;
    align-items: center;
    gap: 9px;
    font-size: 14px;
    line-height: 1;
    margin-bottom: 9px;
  }
  .contacts svg { width: 16px; height: 16px; flex: none; }

  .card--horizontal .brand-mark {
    left: 70px; top: 60px;
    font-size: 80px;
    gap: 10px;
  }
  .card--horizontal .brand-mark__square { width: 60px; height: 60px; }
  .card--horizontal .details { left: 90px; top: 200px; }
  .card--horizontal .details__name { margin-bottom: 12px; }
  .card--horizontal .card__divider { left: 325px; top: 190px; height: 118px; }
  .card--horizontal .contacts { position: absolute; left: 345px; top: 188px; }
</style>
</head>
<body>

<svg width="0" height="0" style="position:absolute">
  <defs>
    <symbol id="icon-phone" viewBox="0 0 16 16"><path d="M3 2h3l1 3-2 1.5c.8 1.8 2 3 3.5 3.5L10 8l3 1v3c0 .6-.4 1-1 1C6.5 13 3 9.5 3 3c0-.6.4-1 0-1z" fill="var(--icon)"/></symbol>
    <symbol id="icon-mobile" viewBox="0 0 16 16"><rect x="4.5" y="1" width="7" height="14" rx="1.5" fill="var(--icon)"/><rect x="6" y="3" width="4" height="8" fill="#fff"/></symbol>
    <symbol id="icon-fax" viewBox="0 0 16 16"><rect x="1" y="6" width="14" height="7" rx="1.5" fill="var(--icon)"/><rect x="4" y="2" width="8" height="5" fill="var(--icon)" opacity=".6"/><rect x="4" y="9" width="8" height="2" fill="#fff"/></symbol>
    <symbol id="icon-at" viewBox="0 0 16 16"><circle cx="8" cy="8" r="6.5" fill="none" stroke="var(--icon)" stroke-width="1.6"/><circle cx="8" cy="8" r="2.4" fill="none" stroke="var(--icon)" stroke-width="1.6"/></symbol>
    <symbol id="icon-web" viewBox="0 0 16 16"><circle cx="8" cy="8" r="6.5" fill="var(--icon)"/><path d="M1.5 8h13M8 1.5c-3 3-3 10 0 13M8 1.5c3 3 3 10 0 13" fill="none" stroke="#fff" stroke-width=".9"/></symbol>
  </defs>
</svg>

<article class="card card--vertical">
  <div class="card__band"></div>
  <div class="brand-mark"><span class="brand-mark__square"></span><span>TORV</span></div>
  <div class="card__divider"></div>
  <div class="details">
    <p class="details__name">VIKRAM TULSE</p>
    <p class="details__address">D-47, West Enclave-II,<br>Gurgaon 122001,<br>Haryana, India</p>
    <ul class="contacts">
      <li><svg><use href="#icon-phone"/></svg>+91-124-5550182</li>
      <li><svg><use href="#icon-mobile"/></svg>+91-9000555123</li>
      <li><svg><use href="#icon-fax"/></svg>+91-124-5550947</li>
      <li><svg><use href="#icon-at"/></svg>vikram@torv.co.in</li>
      <li><svg><use href="#icon-web"/></svg>www.torv.co.in</li>
    </ul>
  </div>
</article>

<article class="card card--horizontal">
  <div class="card__band"></div>
  <div class="brand-mark"><span class="brand-mark__square"></span><span>TORV</span></div>
  <div class="details">
    <p class="details__name">VIKRAM TULSE</p>
    <p class="details__address">D-47, West Enclave-II,<br>Gurgaon 122001,<br>Haryana, India</p>
  </div>
  <div class="card__divider"></div>
  <ul class="contacts">
    <li><svg><use href="#icon-phone"/></svg>+91-124-5550182</li>
    <li><svg><use href="#icon-mobile"/></svg>+91-9000555123</li>
    <li><svg><use href="#icon-fax"/></svg>+91-124-5550947</li>
    <li><svg><use href="#icon-at"/></svg>vikram@torv.co.in</li>
    <li><svg><use href="#icon-web"/></svg>www.torv.co.in</li>
  </ul>
</article>

</body>
</html>
```